Business cards in digital learning for freelancer

Hello, I need a business cards in french. I work in the Digital learning industries as freeelancer; I'm an expert in digital learning. I work in France. My customer are in the health industry, pharmaceutical industry, and training organization. I've got a logo. I offer three services: consulting, Design, and Training. In the consulting, I offers coaching to choose your digital learning tools and the digital learning strategy. For the Design, I product differents level of elearning like rapid-learning, elearning, micro-learning, video-learning. And for the training service, I've create training about pedagogy, digital learning management project, Digital learning design.
I join my Logo create in this platform. My universe is gamified. I like the life, and I'm very social. I want a card like I'm I. I love Art (painting), Europeen comics. I use in my visual support "permanent maker" font and caracters. I would like cards: elegant, modern, Top class. If you need any information, you can ask me.
thanks for ideas

Target Market(s)

in health industries and training organization for Training manager, instructor, human resources director

Contact Information for Business Card

Phone number : 06 71 38 95 14 , mail: bastiengolmier@quelmoto.fr, web: bastiengolmier.fr , Carrivo

Font styles to use
Sans Serif

Requirements
Must have
• Use my logo and write my 3 services (consulting, training, design)

```html
<!DOCTYPE html>
<html lang="fr">
<head>
<meta charset="utf-8">
<title>Golmier Digital Learning – Cartes de visite</title>
<link rel="stylesheet" href="https://fonts.googleapis.com/css2?family=Arimo:wght@400;700&family=Oswald:wght@600&display=swap">
<style>
  :root {
    --backdrop: #141414;
    --card: #1e1e1e;
    --orange: #f27a21;
    --grey-text: #a6a6a6;
    --white-text: #f2f2f2;
    --rule: #4a4a4a;
    --social-blue: #1a73b5;
  }
  * { box-sizing: border-box; margin: 0; padding: 0; }
  html, body { width: 1200px; height: 900px; overflow: hidden; }
  body {
    background: var(--backdrop);
    font-family: "Arimo", Arial, sans-serif;
    position: relative;
  }
  .card {
    position: absolute;
    left: 320px;
    width: 560px;
    height: 320px;
    background: var(--card);
    box-shadow: 0 10px 30px rgba(0,0,0,0.6);
  }
  .card--front { top: 100px; }
  .card--back { top: 480px; }

  /* Front */
  .brand {
    position: absolute;
    top: 100px; left: 0; right: 0;
    text-align: center;
  }
  .brand__name {
    color: var(--orange);
    font-weight: 700;
    font-size: 34px;
    letter-spacing: 1px;
  }
  .social {
    position: absolute;
    top: 200px; left: 60px; right: 60px;
    display: flex; align-items: center; gap: 14px;
  }
  .social__rule { flex: 1; height: 1px; background: var(--rule); }
  .social__badge {
    display: flex; align-items: center; gap: 6px;
    color: var(--grey-text); font-size: 13px;
  }
  .social__dot {
    width: 18px; height: 18px; border-radius: 50%;
    background: var(--social-blue);
  }

  /* Back */
  .holder {
    position: absolute; top: 105px; left: 70px;
  }
  .holder__name {
    font-family: "Oswald", "Arial Narrow", sans-serif;
    font-weight: 600;
    color: var(--orange);
    font-size: 26px;
    text-transform: uppercase;
    line-height: 1.1;
  }
  .holder__role { color: var(--grey-text); font-size: 17px; }
  .divider {
    position: absolute; top: 110px; left: 262px;
    width: 1px; height: 78px; background: var(--grey-text);
  }
  .contacts {
    position: absolute; top: 116px; left: 288px;
    list-style: none;
  }
  .contacts li {
    display: flex; align-items: center; gap: 9px;
    color: var(--grey-text); font-size: 15px;
    height: 22px;
  }
  .contacts svg { width: 14px; height: 14px; flex: none; }
  .services {
    position: absolute; bottom: 42px; left: 0; right: 0;
    text-align: center;
    color: var(--white-text);
    font-size: 14px;
    letter-spacing: 0.5px;
    text-transform: uppercase;
  }
  .services__dot {
    display: inline-block; width: 9px; height: 9px; border-radius: 50%;
    background: var(--orange); margin: 0 6px; vertical-align: 1px;
  }
</style>
</head>
<body>
  <section class="card card--front" aria-label="Recto">
    <div class="brand">
      <p class="brand__name">Golmier Digital Learning</p>
    </div>
    <div class="social">
      <span class="social__rule"></span>
      <span class="social__badge"><span class="social__dot"></span>Carrivo</span>
      <span class="social__rule"></span>
    </div>
  </section>

  <section class="card card--back" aria-label="Verso">
    <div class="holder">
      <p class="holder__name">Bastien Golmier</p>
      <p class="holder__role">Managing Director</p>
    </div>
    <span class="divider"></span>
    <ul class="contacts">
      <li>
        <svg viewBox="0 0 16 16" aria-hidden="true"><path fill="#f27a21" d="M3.6 1.5l2.3 2.6-1.2 1.6c.8 1.9 2.3 3.4 4.3 4.3l1.6-1.2 2.6 2.3-1.4 2.2C7 13 3 9 1.6 2.9z"/></svg>
        06 71 38 95 14
      </li>
      <li>
        <svg viewBox="0 0 16 16" aria-hidden="true"><rect x="1" y="3" width="14" height="10" fill="#f27a21"/><path d="M1 3l7 6 7-6" fill="none" stroke="#1e1e1e" stroke-width="1.3"/></svg>
        bastiengolmier@quelmoto.fr
      </li>
      <li>
        <svg viewBox="0 0 16 16" aria-hidden="true"><g fill="none" stroke="#f27a21" stroke-width="1.3"><circle cx="8" cy="8" r="6.5"/><ellipse cx="8" cy="8" rx="3" ry="6.5"/><path d="M1.5 8h13M2.5 4.8h11M2.5 11.2h11"/></g></svg>
        www.bastiengolmier.fr
      </li>
    </ul>
    <p class="services">Consulting<span class="services__dot"></span>Training<span class="services__dot"></span>Design</p>
  </section>
</body>
</html>
```